Web Design for a Biotech Consulting Firm

We need a web site design for a new business based in Philadelphia called Verantel Dx. This is a consulting firm that will serve medical diagnostics industry, which is part of the life science/healthcare industry focusing on developing and marketing products that help in early detection, monitoring or management of diseases. Our consulting firm will help medical diagnostic companies to overcome key challenges in designing, evaluating and marketing new products.Our company name is Verantel Dx. Verantel is Latin word for "something" Dx represents diagnostics. The idea behind the name is that we help companies to transform the original, early product ideas ("nothing") into "something"; which is a product with full clinical utility that will help to improve health and well-being.The web site should use the visual feel of the logo (attached), be modern, simple and clean looking and represent creativity, innovation, scientific thinking and progress.
Updates

Wix Design is acceptable

Industry/Entity Type

Biotechnology

Coding

Coded - Design and coding required

Number of Pages Required

1 page

Font styles to use
Sans Serif

Requirements
Must have
• simple, clean look couple of pages
Should not have
• a lot of pages

```html
<!DOCTYPE html>
<html lang="en">
<head>
<meta charset="utf-8">
<title>Verantel Dx</title>
<link href="https://fonts.googleapis.com/css2?family=Montserrat:wght@400;500;600&family=Raleway:wght@400;500&display=swap" rel="stylesheet">
<style>
:root{
  --ink:#1b1b1b;
  --dark:#1e1e1e;
  --blue:#1a82f7;
  --blue-soft:#3a95f9;
  --card:#eef4fd;
  --text:#666;
  --white:#fff;
}
*{box-sizing:border-box;margin:0;padding:0}
html,body{width:1200px;height:3125px;overflow:hidden}
body{font-family:'Raleway',sans-serif;color:var(--ink);background:var(--white);position:relative}
.wrap{width:1046px;margin:0 auto;position:relative;height:100%}
h1,h2,h3,.brand{font-family:'Montserrat',sans-serif}
.accent{color:var(--blue)}

/* header */
.site-header{height:125px;background:var(--dark);position:relative}
.brand{position:absolute;left:0;top:48px;color:var(--white);font-size:20px;font-weight:500;white-space:nowrap;line-height:28px}
.contact-bar{position:absolute;right:0;top:20px;display:flex;gap:50px;color:var(--white);font-family:'Montserrat',sans-serif;font-size:16px}
.contact-bar span{display:flex;align-items:center;gap:14px}
.main-nav{position:absolute;right:0;top:77px;display:flex;font-size:13px;color:var(--white)}
.main-nav a{color:inherit;text-decoration:none;padding:0 34px;border-left:1px solid #555;line-height:16px}
.main-nav a:first-child{border-left:0}
.main-nav a:last-child{padding-right:0}
.main-nav a.active{color:var(--blue)}

/* hero */
.hero{height:552px;position:relative;background:linear-gradient(90deg,#f3f5f8 0%,#e6eaef 40%,#c9d2dc 70%,#b7c1cc 100%)}
.hero-copy{position:absolute;left:80px;top:172px}
.hero h1{font-size:44px;font-weight:600;line-height:62px}
.hero p{margin-top:28px;font-size:17px;line-height:29px;color:#333;width:450px}

/* welcome */
.welcome{height:353px;text-align:center;padding-top:52px}
.welcome h2,.section-title{font-size:39px;font-weight:600}
.welcome p{width:740px;margin:0 auto;font-size:13.5px;line-height:25px;color:var(--text)}
.welcome h2{margin-bottom:26px}
.welcome p+p{margin-top:16px}

/* services */
.services{height:740px;background:var(--dark);text-align:center;padding-top:46px;position:relative}
.services .section-title{color:var(--white)}
.services .lead{color:#ddd;font-size:13.5px;line-height:25px;width:650px;margin:22px auto 0}
.cards{display:flex;justify-content:space-between;position:absolute;top:211px;left:77px;right:77px}
.service-card{width:323px;height:438px;background:var(--card);border-radius:4px;overflow:hidden;position:relative}
.service-card .photo{height:218px}
.service-icon{position:absolute;left:120px;top:177px;width:84px;height:84px;background:var(--card);display:flex;align-items:center;justify-content:center}
.service-card h3{margin-top:68px;font-size:18px;font-weight:500;letter-spacing:.5px}
.service-card p{margin:22px 20px 0;font-size:13.5px;line-height:25px;color:var(--text)}
.notch{position:absolute;left:580px;bottom:-20px;width:0;height:0;border-left:20px solid transparent;border-right:20px solid transparent;border-top:20px solid var(--dark);z-index:2}

/* testimonials */
.testimonials{height:541px;background:var(--blue);position:relative;text-align:center;padding-top:70px}
.testimonials .section-title{color:var(--white)}
.quote-box{position:absolute;left:267px;top:200px;width:666px;height:229px;background:var(--blue-soft);color:var(--white)}
.avatar{position:absolute;left:558px;top:156px;width:84px;height:84px;border-radius:50%;background:linear-gradient(#e6edf5,#c3d0de);border:2px solid var(--white);z-index:2}
.quote-box h3{margin-top:64px;font-size:21px;font-weight:500}
.quote-box p{margin:18px 28px 0;font-size:13.5px;line-height:25px}
.dots{position:absolute;top:457px;left:0;right:0;display:flex;justify-content:center;gap:5px}
.dots i{width:13px;height:13px;border:1.5px solid var(--white);border-radius:50%}
.dots i:first-child{background:var(--white)}

/* news */
.news{height:637px;text-align:center;padding-top:48px;position:relative}
.news-grid{position:absolute;top:116px;left:77px;right:77px;display:flex;justify-content:space-between;text-align:left}
.news-card{width:323px}
.news-photo{height:218px;position:relative;border-radius:3px;background:linear-gradient(135deg,#c9d4df,#8fa2b7)}
.date-badge{position:absolute;right:30px;top:180px;width:62px;height:73px;background:var(--blue);color:var(--white);text-align:center;font-family:'Montserrat',sans-serif}
.date-badge b{display:block;font-size:25px;font-weight:600;padding-top:10px}
.date-badge small{font-size:13px}
.news-card .meta{margin:42px 2px 0;font-size:13.5px;color:var(--blue)}
.news-card h3{margin:14px 0 0 2px;font-size:17.5px;font-weight:500;line-height:29px;letter-spacing:-.1px;white-space:nowrap}
.news-card p{margin:15px 2px 0;font-size:13.5px;line-height:25px;color:#555}

/* footer */
.site-footer{height:177px;background:var(--dark);color:var(--white)}
.footer-contacts{height:105px;display:flex;border-bottom:1px solid #333}
.footer-contacts div{flex:0 0 auto;display:flex;align-items:center;justify-content:center;gap:22px;font-size:13.5px;line-height:25px;border-left:1px solid #3a3a3a}
.footer-contacts div:first-child{border-left:0;width:420px}
.footer-contacts div:nth-child(2){width:361px}
.footer-contacts div:nth-child(3){width:419px}
.copyright{text-align:center;font-size:13.5px;line-height:72px}
</style>
</head>
<body>

<header class="site-header">
  <div class="wrap">
    <div class="brand">Verantel Dx</div>
    <div class="contact-bar">
      <span><svg width="22" height="16" viewBox="0 0 22 16"><rect x="1" y="1" width="20" height="14" fill="none" stroke="#1a82f7" stroke-width="2"/><path d="M1 1l10 8 10-8" fill="none" stroke="#1a82f7" stroke-width="2"/></svg>info@verantel-dx.com</span>
      <span><svg width="20" height="20" viewBox="0 0 24 24"><path d="M6.6 10.8a15.1 15.1 0 006.6 6.6l2.2-2.2a1 1 0 011-.25 11.4 11.4 0 003.6.57 1 1 0 011 1V20a1 1 0 01-1 1A17 17 0 013 4a1 1 0 011-1h3.5a1 1 0 011 1 11.4 11.4 0 00.57 3.6 1 1 0 01-.25 1z" fill="#1a82f7"/></svg>215 555 0148</span>
    </div>
    <nav class="main-nav">
      <a href="#" class="active">HOME</a><a href="#">ABOUT</a><a href="#">SERVICES</a><a href="#">NEWS</a><a href="#">CONTACT</a>
    </nav>
  </div>
</header>

<section class="hero" role="img" aria-label="Photo of doctors in white coats working together at a laptop">
  <div class="hero-copy">
    <h1>Lorem Ipsum is<br>simply <span class="accent">dummy text.</span></h1>
    <p>Lorem Ipsum is simply dummy text of the printing and typesetting industry. Lorem Ipsum has been the.</p>
  </div>
</section>

<section class="welcome">
  <h2>Welcome to Verantel <span class="accent">Dx</span></h2>
  <p>Lorem Ipsum is simply dummy text of the printing and typesetting industry. Lorem Ipsum has been the industry's standard dummy text ever since the 1500s, when an unknown printer took a galley of type and scrambled it to make a type specimen book including versions of Lorem Ipsum..</p>
  <p>It has survived not only five centuries, but also the leap into electronic typesetting, remaining essentially unchanged. It was popularised in the 1960s with the release of Letraset sheets containing Lorem Ipsum passages, and more recently with desktop publishing software like Aldus PageMaker.</p>
</section>

<section class="services">
  <h2 class="section-title">Our <span class="accent">Services</span></h2>
  <p class="lead">Lorem Ipsum is simply dummy text of the printing and typesetting industry. Lorem Ipsum has been the industry's standard dummy text ever since the 1500s, when an unknown printer took.</p>
  <div class="cards">
    <article class="service-card">
      <div class="photo" role="img" aria-label="Photo of a microscope and a doctor holding a tablet" style="background:linear-gradient(135deg,#d9cfc9,#f1e9e4 60%,#cfc5c0)"></div>
      <div class="service-icon"><svg width="52" height="52" viewBox="0 0 52 52" fill="none" stroke="#1a82f7" stroke-width="2"><rect x="6" y="12" width="40" height="32"/><rect x="10" y="16" width="32" height="24"/><circle cx="26" cy="10" r="6"/><path d="M20 28l-3 3 3 3M32 28l3 3-3 3M28 26l-4 10"/></svg></div>
      <h3>DEVELOPMENT</h3>
      <p>Lorem Ipsum is simply dummy text of the printing and typesetting indust Lorem Ipsum has been the industry's standard dummy.</p>
    </article>
    <article class="service-card">
      <div class="photo" role="img" aria-label="Photo of two lab scientists in caps and masks reviewing a tablet" style="background:linear-gradient(135deg,#dfe6ec,#b9c8d6 60%,#e7ecf0)"></div>
      <div class="service-icon"><svg width="52" height="52" viewBox="0 0 52 52" fill="none" stroke="#1a82f7" stroke-width="2"><circle cx="24" cy="28" r="20"/><circle cx="24" cy="28" r="13"/><circle cx="24" cy="28" r="6"/><path d="M24 28L44 8M38 8h6v6"/></svg></div>
      <h3>MARKETING</h3>
      <p>Lorem Ipsum is simply dummy text of the printing and typesetting indust Lorem Ipsum has been the industry's standard dummy.</p>
    </article>
    <article class="service-card">
      <div class="photo" role="img" aria-label="Photo of a doctor next to a digital patient records screen" style="background:linear-gradient(90deg,#a9bccc,#d3dde6 60%,#eef1f4)"></div>
      <div class="service-icon"><svg width="54" height="48" viewBox="0 0 54 48" fill="none" stroke="#1a82f7" stroke-width="2"><rect x="3" y="4" width="48" height="32" rx="2"/><path d="M22 44h10M27 36v8M9 22h9l4-8 6 14 4-8h13"/></svg></div>
      <h3>MONITORING</h3>
      <p>Lorem Ipsum is simply dummy text of the printing and typesetting indust Lorem Ipsum has been the industry's standard dummy.</p>
    </article>
  </div>
  <div class="notch"></div>
</section>

<section class="testimonials">
  <h2 class="section-title">Client Testimonials</h2>
  <div class="avatar" role="img" aria-label="Client portrait"></div>
  <div class="quote-box">
    <h3>- Client Name</h3>
    <p>Lorem Ipsum is simply dummy text of the printing and typesetting industry. Lorem Ipsum has been the industry's standard dummy text ever since the 1500s, when an unknown printer took a galley of type and scrambled it to make a type specimen book.</p>
  </div>
  <div class="dots"><i></i><i></i><i></i><i></i></div>
</section>

<section class="news">
  <h2 class="section-title">Latest <span class="accent">News</span></h2>
  <div class="news-grid">
    <article class="news-card">
      <div class="news-photo" role="img" aria-label="Photo of scientists working at a lab screen"><div class="date-badge"><b>20</b><small>MAR</small></div></div>
      <div class="meta">POSTED BY ADMIN</div>
      <h3>Lorem Ipsum is simply dummy text<br>of the printing and typesetting.</h3>
      <p>Lorem Ipsum is simply dummy text of the printing and typesetting industry. Lorem Ipsum has been the industry's standard dummy text ever since the 1500s, when an unknown printer took a galley.</p>
    </article>
    <article class="news-card">
      <div class="news-photo" role="img" aria-label="Photo of nurses looking at a monitor" style="background:linear-gradient(135deg,#6f8fb5,#c7d3e0)"><div class="date-badge"><b>20</b><small>MAR</small></div></div>
      <div class="meta">POSTED BY ADMIN</div>
      <h3>Lorem Ipsum is simply dummy text<br>of the printing and typesetting.</h3>
      <p>Lorem Ipsum is simply dummy text of the printing and typesetting industry. Lorem Ipsum has been the industry's standard dummy text ever since the 1500s, when an unknown printer took a galley.</p>
    </article>
    <article class="news-card">
      <div class="news-photo" role="img" aria-label="Photo of a medical team meeting around a laptop" style="background:linear-gradient(135deg,#9fb0c2,#dde3ea)"><div class="date-badge"><b>20</b><small>MAR</small></div></div>
      <div class="meta">POSTED BY ADMIN</div>
      <h3>Lorem Ipsum is simply dummy text<br>of the printing and typesetting.</h3>
      <p>Lorem Ipsum is simply dummy text of the printing and typesetting industry. Lorem Ipsum has been the industry's standard dummy text ever since the 1500s, when an unknown printer took a galley.</p>
    </article>
  </div>
</section>

<footer class="site-footer">
  <div class="footer-contacts">
    <div><svg width="16" height="24" viewBox="0 0 16 24"><path d="M8 0a8 8 0 00-8 8c0 6 8 16 8 16s8-10 8-16a8 8 0 00-8-8zm0 11a3 3 0 110-6 3 3 0 010 6z" fill="#1a82f7"/></svg><span>Lorem Ipsum is simply dummy<br>text of the printing.</span></div>
    <div><svg width="22" height="22" viewBox="0 0 24 24"><path d="M6.6 10.8a15.1 15.1 0 006.6 6.6l2.2-2.2a1 1 0 011-.25 11.4 11.4 0 003.6.57 1 1 0 011 1V20a1 1 0 01-1 1A17 17 0 013 4a1 1 0 011-1h3.5a1 1 0 011 1 11.4 11.4 0 00.57 3.6 1 1 0 01-.25 1z" fill="#1a82f7"/></svg><span>CALL US:<br>215 555 0148</span></div>
    <div><svg width="22" height="16" viewBox="0 0 22 16"><rect x="1" y="1" width="20" height="14" fill="none" stroke="#1a82f7" stroke-width="2"/><path d="M1 1l10 8 10-8" fill="none" stroke="#1a82f7" stroke-width="2"/></svg><span>EMAIL US:<br>info@verantel-dx.com</span></div>
  </div>
  <div class="copyright">©Verantel Dx. 2019 - All Rights Reserved.</div>
</footer>

</body>
</html>
```